Tidy paddock Services

After a high quality design website. we are a company that provides services to people that own land and need a hand getting on top of the delayed jobs.
would want a number of tab/ pages for the web page.
Home page / About us page / services page / Gallery page. / Contact us page
we offer a wide range of services .listed below

Stock Work (title)

Stock movement
Break feeding
Temporary staffing

Spraying (title)

Spraying weeds
Spraying gorse

Pastures (title)

Fertilizing
Topping

Building (title)

Habitable sheds
Farm sheds
Sheep yards
Cattle yards
Repair farm buildings
Decks
Retaining walls

Fencing (title)

Stock fencing
Post & rail
Stock yards repair
Electric fencing install & repairs

Water Management (title)

Water trough installation
Water scheme install
Water trough cleaning
Farm water maintenance
Water ponds
Ornamental ponds
Drainage

General (title)

Lawn mowing
Hedge trimming
Pruning trees
Metaling drive ways & races
Water blasting
Small digger work
Little tip truck cartage
Home kill management
Mulching gorse
Section clearing

```html
<!DOCTYPE html>
<html lang="en">
<head>
<meta charset="utf-8">
<title>Tidy Paddock Services</title>
<link href="https://fonts.googleapis.com/css2?family=Montserrat:wght@500;600;700&family=Lato:wght@400;700&display=swap" rel="stylesheet">
<style>
:root{
  --green:#6a9b1c;
  --ink:#111111;
  --text:#222222;
  --grey-pill:#e3e3e3;
  --lavender:#eef0fa;
  --footer:#0b0b0b;
  --white:#ffffff;
}
*{margin:0;padding:0;box-sizing:border-box}
html,body{width:1200px;height:3215px;overflow:hidden;background:var(--white)}
body{position:relative;font-family:'Lato',sans-serif;color:var(--text)}
.abs{position:absolute}
.mont{font-family:'Montserrat',sans-serif}
.topbar{top:0;left:0;width:1200px;height:7px;background:linear-gradient(90deg,var(--green) 50%,var(--ink) 50%)}
.brand{display:flex;align-items:center;gap:12px;font-family:'Montserrat',sans-serif;font-weight:700;color:var(--green);font-size:26px;line-height:1.05}
.brand-dot{width:22px;height:22px;border-radius:50%;background:var(--green);flex:none}
.contact-line{top:62px;font-family:'Montserrat',sans-serif;font-weight:600;font-size:14px;color:var(--ink);display:flex;align-items:center;gap:8px}
.quote-btn{top:55px;left:1020px;width:118px;height:36px;border-radius:18px;background:linear-gradient(90deg,#111,#2c3a10);color:#fff;font:700 12px 'Montserrat',sans-serif;display:flex;align-items:center;justify-content:center}
.nav{top:117px;font:600 16px 'Montserrat',sans-serif;color:var(--ink)}
.nav.active{color:var(--green);text-decoration:underline;text-underline-offset:4px}
.hero-welcome{top:252px;left:111px;font:600 16px 'Montserrat',sans-serif;color:var(--ink)}
.hero-title{top:284px;left:109px;font:700 50px 'Montserrat',sans-serif;color:var(--green);letter-spacing:1px}
.hero-sub{top:360px;left:111px;font:600 16px 'Montserrat',sans-serif;letter-spacing:4px;color:var(--ink)}
.hero-text{top:397px;left:111px;width:460px;font-size:15px;line-height:27px;color:var(--text)}
.btn-dark{top:497px;left:111px;width:165px;height:51px;border-radius:26px;background:linear-gradient(90deg,#111,#2c3a10);color:#fff;font:700 16px 'Montserrat',sans-serif;display:flex;align-items:center;justify-content:center}
.section-title{left:0;width:1200px;text-align:center;font:700 32px 'Montserrat',sans-serif;color:var(--ink)}
.about-text{left:160px;width:880px;text-align:center;color:#fff;font-size:15.5px;line-height:27.5px}
.btn-light{top:1054px;left:518px;width:164px;height:51px;border-radius:26px;background:#fff;color:var(--green);font:700 16px 'Montserrat',sans-serif;display:flex;align-items:center;justify-content:center}
.tabs{top:1339px;left:112px;width:980px;display:flex;gap:10px}
.tab{flex:1;height:51px;border-radius:26px;background:var(--grey-pill);font:700 12.5px 'Montserrat',sans-serif;color:var(--ink);display:flex;align-items:center;justify-content:center;text-align:center;white-space:nowrap;padding:0 6px}
.tab.wide{flex:1.35}
.tab.active{background:var(--green);color:#fff}
.card{top:1446px;width:284px;height:298px;border-radius:14px;background:#fff;box-shadow:0 4px 14px rgba(0,0,0,.12);overflow:hidden}
.card-img{height:231px}
.card-label{height:67px;display:flex;align-items:center;justify-content:center;font:700 16px 'Montserrat',sans-serif;color:var(--ink)}
.avatar{border-radius:50%}
.quote-mark{font:700 190px/1 'Montserrat',sans-serif;color:#d9dbe3}
.dot{width:12px;height:12px;border-radius:50%;background:#cfd2dc}
.foot-head{top:2887px;font:500 19px 'Montserrat',sans-serif;color:#fff}
.foot-list{list-style:none;color:#fff;font-size:15px}
.foot-list li{height:34.3px;display:flex;align-items:center;gap:10px}
.social{top:3051px;width:32px;height:32px;border-radius:50%;background:#fff}
.contact-item{left:854px;display:flex;gap:14px;color:#ddd;font-size:15px;line-height:27px}
.ic{width:32px;height:32px;border-radius:50%;background:#fff;display:flex;align-items:center;justify-content:center;flex:none}
</style>
</head>
<body>

<div class="abs topbar"></div>

<header>
  <div class="abs brand" style="top:68px;left:62px"><span class="brand-dot"></span><span>Tidy Paddock<br>Services</span></div>
  <div class="abs contact-line" style="left:489px">
    <svg width="14" height="14" viewBox="0 0 24 24"><path fill="#6a9b1c" d="M6.6 10.8a15.1 15.1 0 0 0 6.6 6.6l2.2-2.2c.3-.3.7-.4 1-.2 1.1.4 2.3.6 3.6.6.6 0 1 .4 1 1V20c0 .6-.4 1-1 1A17 17 0 0 1 3 4c0-.6.4-1 1-1h3.5c.6 0 1 .4 1 1 0 1.3.2 2.5.6 3.6.1.3 0 .7-.2 1z"/></svg>
    Call : +1 555 014 2290</div>
  <div class="abs contact-line" style="left:705px">
    <svg width="14" height="12" viewBox="0 0 24 18"><rect width="24" height="18" rx="2" fill="#6a9b1c"/><path d="M2 3l10 7 10-7" stroke="#fff" stroke-width="2" fill="none"/></svg>
    Email : hello@tidypaddock.example</div>
  <div class="abs quote-btn">GET A QUOTE</div>
  <nav>
    <span class="abs nav active" style="left:468px">HOME</span>
    <span class="abs nav" style="left:586px">ABOUT US</span>
    <span class="abs nav" style="left:743px">SERVICES</span>
    <span class="abs nav" style="left:890px">GALLERY</span>
    <span class="abs nav" style="left:1033px">CONTACT US</span>
  </nav>
</header>

<section class="hero">
  <div class="abs hero-welcome">WELCOME TO</div>
  <div class="abs hero-title">TIDY PADDOCK</div>
  <div class="abs hero-sub">SERVICES</div>
  <p class="abs hero-text">Itaque earum rerum hic tenetur a sapiente delectus, ut aut reiciendis voluptatibus maiores alias consequatur aut perferendis doloribus asperiores repellat.</p>
  <div class="abs btn-dark">GET STARTED</div>
</section>

<svg class="abs" style="top:540px;left:0" width="1200" height="624" viewBox="0 540 1200 624">
  <defs>
    <linearGradient id="aboutBg" x1="0" y1="0" x2="0" y2="1">
      <stop offset="0" stop-color="#6b9c1d"/><stop offset="1" stop-color="#5f901a"/>
    </linearGradient>
  </defs>
  <path d="M0 600 C120 680 260 700 420 670 C620 630 780 560 1000 570 C1100 560 1160 548 1200 545 L1200 1164 L0 1164 Z" fill="url(#aboutBg)"/>
</svg>

<div class="abs" style="top:231px;left:678px;width:450px;height:450px;border-radius:50%;background:#fff"></div>
<div class="abs" role="img" aria-label="Green lawn mower cutting grass in the sun" style="top:238px;left:685px;width:436px;height:436px;border-radius:50%;background:radial-gradient(circle at 60% 45%,#3f8c6d 0%,#6e9d3a 45%,#a9c86a 100%)"></div>

<section class="about">
  <h2 class="abs section-title" style="top:772px;color:#fff">ABOUT TIDY PADDOCK SERVICES</h2>
  <p class="abs about-text" style="top:850px">Nam libero tempore, cum soluta nobis est eligendi optio cumque nihil impedit quo minus id quod maxime placeat facere possimus, omnis voluptas assumenda est, omnis dolor repellendus. Temporibus autem quibusdam et aut officiis debitis aut rerum necessitatibus saepe eveniet ut et voluptates repudiandae sint et molestiae non recusandae.</p>
  <p class="abs about-text" style="top:960px">Itaque earum rerum hic tenetur a sapiente delectus, ut aut reiciendis voluptatibus maiores alias consequatur aut perferendis doloribus asperiores repellat.</p>
  <div class="abs btn-light">READ MORE</div>
</section>

<section class="services">
  <h2 class="abs section-title" style="top:1243px">OUR SERVICES</h2>
  <div class="abs tabs">
    <div class="tab active">STOCK WORK</div>
    <div class="tab">SPRAYING</div>
    <div class="tab">PASTURES</div>
    <div class="tab">BUILDING</div>
    <div class="tab">FENCING</div>
    <div class="tab wide">WATER MANAGEMENT</div>
    <div class="tab">GENERAL</div>
  </div>

  <div class="abs card" style="left:111px">
    <div class="card-img" role="img" aria-label="Rows of young crops in a field at sunrise" style="background:linear-gradient(180deg,#e6c46a 0%,#8a9a4a 40%,#3f5a22 100%)"></div>
    <div class="card-label">STOCK MOVEMENT</div>
  </div>
  <div class="abs card" style="left:458px">
    <div class="card-img" role="img" aria-label="Dairy cows feeding at a trough" style="background:linear-gradient(180deg,#5a5a55 0%,#8a8478 55%,#b49a70 100%)"></div>
    <div class="card-label">BREAK FEEDING</div>
  </div>
  <div class="abs card" style="left:805px">
    <div class="card-img" role="img" aria-label="Worker packing fresh cabbages in a produce shed" style="background:linear-gradient(180deg,#cdbb9c 0%,#7c8a6a 55%,#2f7a5a 100%)"></div>
    <div class="card-label">TEMPORARY STAFFING</div>
  </div>
</section>

<section class="abs" style="top:1817px;left:0;width:1200px;height:622px;background:var(--lavender)">
  <h2 class="abs section-title" style="top:75px">WHAT CUSTOMER SAYS</h2>
  <div class="abs avatar" role="img" aria-label="Customer portrait" style="left:542px;top:168px;width:134px;height:134px;background:linear-gradient(180deg,#f2c9a3,#e8b38a)"></div>
  <div class="abs avatar" role="img" aria-label="Customer portrait" style="left:137px;top:243px;width:68px;height:68px;background:linear-gradient(180deg,#e9c2a4,#c9967a)"></div>
  <div class="abs avatar" role="img" aria-label="Customer portrait" style="left:1015px;top:168px;width:48px;height:48px;background:linear-gradient(180deg,#b8b0a8,#6a5e58)"></div>
  <div class="abs avatar" style="left:381px;top:281px;width:14px;height:14px;background:#e5162c"></div>
  <div class="abs avatar" style="left:897px;top:244px;width:6px;height:6px;background:#4a7be0"></div>
  <div class="abs mont" style="top:327px;left:0;width:1200px;text-align:center;font-weight:600;font-size:21px;color:var(--ink)">Mason Keller</div>
  <div class="abs mont" style="top:359px;left:0;width:1200px;text-align:center;font-weight:500;font-size:12px;color:#555">United States</div>
  <div class="abs" style="top:380px;left:0;width:1200px;text-align:center;font-size:30px;color:#f5b325;letter-spacing:1px">★★★★★</div>
  <div class="abs quote-mark" style="top:342px;left:168px">“</div>
  <div class="abs quote-mark" style="top:442px;left:958px">”</div>
  <p class="abs mont" style="top:422px;left:280px;width:660px;text-align:center;font-weight:500;font-size:16px;line-height:26px;color:#222">Itaque earum rerum hic tenetur a sapiente delectus, ut aut reiciendis voluptatibus maiores alias. Consequatur aut perferendis doloribus asperiores repellat.Et harum quidem rerum facilis est et expedita distinctio.</p>
  <div class="abs" style="top:531px;left:553px;display:flex;gap:8.5px">
    <span class="dot"></span><span class="dot"></span><span class="dot"></span><span class="dot" style="background:var(--green)"></span><span class="dot"></span><span class="dot"></span>
  </div>
</section>

<section class="newsletter">
  <h2 class="abs section-title" style="top:2511px">SIGN UP TO OUR NEWSLETTER</h2>
  <p class="abs" style="top:2590px;left:200px;width:800px;text-align:center;font-size:15px;line-height:27px">Itaque earum rerum hic tenetur a sapiente delectus, ut aut reiciendis voluptatibus maiores alias consequatur aut perferendis doloribus asperiores repellat.</p>
  <div class="abs" style="top:2686px;left:154px;width:891px;height:55px;border-radius:28px;background:#fff;box-shadow:0 3px 12px rgba(0,0,0,.1)">
    <span class="abs" style="left:24px;top:19px;font-size:13px;color:#8a8a8a">Enter The Email</span>
    <span class="abs mont" style="right:0;top:0;width:155px;height:55px;border-radius:28px;background:var(--green);color:#fff;font-weight:600;font-size:16px;display:flex;align-items:center;justify-content:center">SUBSCRIBE</span>
  </div>
</section>

<footer class="abs" style="top:2813px;left:0;width:1200px;height:402px;background:var(--footer)"></footer>
<div class="abs brand" style="top:2918px;left:94px;font-size:28px"><span class="brand-dot"></span><span>Tidy Paddock<br>Services</span></div>
<div class="abs social" style="left:110px"></div>
<div class="abs social" style="left:169px"></div>
<div class="abs social" style="left:226px"></div>
<div class="abs social" style="left:284px"></div>

<div class="abs foot-head" style="left:431px">QUICK LINKS</div>
<ul class="abs foot-list" style="top:2925px;left:431px">
  <li>➔ Home</li><li>➔ About</li><li>➔ Services</li><li>➔ Gallery</li><li>➔ Contact Us</li>
</ul>
<div class="abs foot-head" style="left:644px">HELP LINKS</div>
<ul class="abs foot-list" style="top:2925px;left:644px">
  <li>➔ FAQ</li><li>➔ Terms of use</li><li>➔ Privacy Policy</li><li>➔ Support Links</li><li>➔ Conditions</li>
</ul>
<div class="abs foot-head" style="left:854px">CONTACT US</div>
<div class="abs contact-item" style="top:2928px">
  <span class="ic"><svg width="14" height="18" viewBox="0 0 24 32"><path d="M12 0C5.4 0 0 5.4 0 12c0 9 12 20 12 20s12-11 12-20C24 5.4 18.6 0 12 0zm0 17a5 5 0 1 1 0-10 5 5 0 0 1 0 10z" fill="#111"/></svg></span>
  <span>Tidy Paddock Services<br>United States</span>
</div>
<div class="abs contact-item" style="top:2998px">
  <span class="ic"><svg width="15" height="15" viewBox="0 0 24 24"><path fill="#111" d="M6.6 10.8a15.1 15.1 0 0 0 6.6 6.6l2.2-2.2c.3-.3.7-.4 1-.2 1.1.4 2.3.6 3.6.6.6 0 1 .4 1 1V20c0 .6-.4 1-1 1A17 17 0 0 1 3 4c0-.6.4-1 1-1h3.5c.6 0 1 .4 1 1 0 1.3.2 2.5.6 3.6.1.3 0 .7-.2 1z"/></svg></span>
  <span style="line-height:32px">+1 555 014 2290</span>
</div>
<div class="abs contact-item" style="top:3049px">
  <span class="ic"><svg width="15" height="11" viewBox="0 0 24 18"><rect width="24" height="18" rx="2" fill="#111"/><path d="M2 3l10 7 10-7" stroke="#fff" stroke-width="2" fill="none"/></svg></span>
  <span style="line-height:32px">hello@tidypaddock.example</span>
</div>
<div class="abs" style="top:3135px;left:111px;width:978px;height:1px;background:#777"></div>
<div class="abs" style="top:3170px;left:0;width:1200px;text-align:center;color:#fff;font-size:15px">Copyrights@2024.Tidy Paddock Services.All Rights Reserved</div>

</body>
</html>
```